Business card for a Exhibition booth fabrication company

Hi. My company would like to change our corporate name card. We are an events and Exhibition stand builder company. We would like our corporate name card to resonate what we do. I need someone to create something unique that relates to the industry that I am in. The graphic designer should be creative to incorporate the elements of my industry and try to blend in well in the design of the card. Our aim is to ensure that we are unique and our card can look different from our competitors.
Updates

Target Market(s)

Marketing and events manager from all companies

Contact Information for Business Card

The business card should have the following details:
Name
Job Title
Email
Website

Colors

Designer to choose colors to be used in the design.

Requirements
Must have
• The card must be look something that is relevant to the service that I am providing. My website is: www.velmora-buildworks.com
• You can see my website to get more information on what service that I am doing
Nice to have
• On the back of my card, I would like to have a globe image with the incorporation of my company logo. This is to indicate that my services can be done in any part of the world.

```html
<!DOCTYPE html>
<html lang="en">
<head>
<meta charset="utf-8">
<title>Velmora Buildworks – Business Card</title>
<link href="https://fonts.googleapis.com/css2?family=Oswald:wght@600&family=Work+Sans:wght@400;600&display=swap" rel="stylesheet">
<style>
  :root {
    --backdrop: #161616;
    --card: #222222;
    --card-light: #2c2c2c;
    --accent: #e8232b;
    --ink: #f2f2f2;
    --ink-soft: #d9d9d9;
  }
  * { margin: 0; padding: 0; box-sizing: border-box; }
  html, body {
    width: 1200px; height: 900px; overflow: hidden;
    background: var(--backdrop);
    font-family: "Work Sans", Arial, sans-serif;
    color: var(--ink);
  }
  .stage {
    width: 1200px; height: 900px;
    display: flex; flex-direction: column; align-items: center; justify-content: center;
    gap: 40px;
  }
  .card {
    position: relative;
    width: 700px; height: 390px;
    background: linear-gradient(135deg, var(--card) 0%, var(--card) 55%, var(--card-light) 100%);
    border-bottom: 6px solid var(--accent);
    box-shadow: 0 10px 30px rgba(0,0,0,.55);
  }
  /* front */
  .card-front { display: flex; align-items: center; justify-content: center; }
  .brand { display: flex; align-items: center; gap: 14px; }
  .brand-dot { width: 16px; height: 16px; border-radius: 50%; background: var(--accent); }
  .brand-name {
    font-weight: 600; font-size: 26px; letter-spacing: 4px;
    text-transform: uppercase; color: var(--ink);
  }
  /* back */
  .card-back { padding: 0 60px; }
  .identity-row {
    position: absolute; top: 120px; left: 70px; right: 50px;
    display: flex; align-items: center;
  }
  .person { text-align: right; padding-right: 28px; }
  .person-name {
    font-family: "Oswald", "Arial Narrow", sans-serif;
    font-weight: 600; font-size: 44px; line-height: 1;
    color: var(--accent); text-transform: uppercase; letter-spacing: .5px;
  }
  .person-title { font-size: 19px; color: var(--ink-soft); margin-top: 8px; letter-spacing: .5px; }
  .divider { width: 2px; height: 92px; background: var(--accent); }
  .contacts { list-style: none; padding-left: 28px; }
  .contacts li {
    display: flex; align-items: center; gap: 8px;
    font-size: 17px; line-height: 25px; letter-spacing: .6px; color: var(--ink);
  }
  .contacts svg { width: 12px; height: 12px; flex: none; }
  .address {
    position: absolute; bottom: 36px; left: 0; right: 0;
    text-align: center; font-size: 18px; letter-spacing: .8px; color: var(--ink);
  }
</style>
</head>
<body>
<main class="stage">
  <section class="card card-front">
    <div class="brand">
      <span class="brand-dot"></span>
      <span class="brand-name">Velmora Buildworks</span>
    </div>
  </section>

  <section class="card card-back">
    <div class="identity-row">
      <div class="person">
        <h1 class="person-name">Daniel Rourke</h1>
        <p class="person-title">Director</p>
      </div>
      <div class="divider"></div>
      <ul class="contacts">
        <li>
          <svg viewBox="0 0 12 12"><path d="M3 1 L5 3.5 L4 5 Q5 7 7 8 L8.5 7 L11 9 L9.5 11 Q4 10.5 1 3 Z" fill="var(--accent)"/></svg>
          +65 81472096
        </li>
        <li>
          <svg viewBox="0 0 12 12"><rect x="3" y="1" width="6" height="10" rx="1" fill="none" stroke="var(--accent)" stroke-width="1.4"/></svg>
          +974 55208143
        </li>
        <li>
          <svg viewBox="0 0 12 12"><rect x="1" y="2.5" width="10" height="7" fill="none" stroke="var(--accent)" stroke-width="1.2"/><path d="M1 2.5 L6 6.5 L11 2.5" fill="none" stroke="var(--accent)" stroke-width="1.2"/></svg>
          info@velmora-buildworks.com
        </li>
        <li>
          <svg viewBox="0 0 12 12"><circle cx="6" cy="6" r="5" fill="none" stroke="var(--accent)" stroke-width="1.2"/><ellipse cx="6" cy="6" rx="2.2" ry="5" fill="none" stroke="var(--accent)" stroke-width="1"/><path d="M1 6 H11" stroke="var(--accent)" stroke-width="1"/></svg>
          www.velmora-buildworks.com
        </li>
      </ul>
    </div>
    <p class="address">P.O. Box 4120 Marlow Street Doha - Qatar</p>
  </section>
</main>
</body>
</html>
```